Local Flower Farm Needs Business Card Design

I need business cards designed for a flower farm based in Eudora, Kansas.
Business Info:
We are a local cut flower farm located in Eudora, Kansas, founded by Corinne Haldwick. What started as a passion for agriculture and search for more joy in daily life has blossomed into a small business dedicated to providing the community with beautiful, fresh, and sustainable flowers. We specialize in local, seasonal blooms, ensuring that every petal reflects the care and dedication we pour into our craft. Our mission is to deliver the highest quality flowers directly to our customers through local farmers markets and to florists who share our commitment to sustainability. Join us in celebrating the beauty of nature, one bloom at a time!
Contact Details:
Corinne Haldwick
Owner
Phone 913-555-0147
Facebook: Rosalind Thorpe Gardens
Instagram: @RosalindThorpeGardens
Website: RosalindThorpeGardens.example
Target Market(s)
Wholesale to Florists and Direct to Consumer via Farmers Market
Industry/Entity Type
Florist, Farm
Contact Information for Business Card
Name, Contact Info, Logo
Look and feel
Each slider illustrates characteristics of the customer's brand and the style your logo design should communicate.

```html
<!DOCTYPE html>
<html lang="en">
<head>
<meta charset="utf-8">
<title>Rosalind Thorpe Gardens – Business Card</title>
<link rel="stylesheet" href="https://fonts.googleapis.com/css2?family=Montserrat:wght@400;500;700&display=swap">
<style>
  :root {
    --backdrop: #9b9b9b;
    --card-white: #ffffff;
    --ink: #0b2a30;
    --forest: #08272c;
    --cream: #f4f4f2;
    --ring-grey: #6d7375;
  }
  * { box-sizing: border-box; margin: 0; padding: 0; }
  html, body {
    width: 1093px; height: 1200px; overflow: hidden;
    background: var(--backdrop);
    font-family: "Montserrat", Arial, sans-serif;
  }
  .canvas { position: relative; width: 1093px; height: 1200px; }

  .card {
    position: absolute; left: 264px; width: 597px; height: 363px;
    border-radius: 20px;
  }
  .card--front { top: 225px; background: var(--card-white); color: var(--ink); }
  .card--back { top: 615px; height: 367px; background: var(--forest); }

  .holder { position: absolute; left: 30px; top: 44px; }
  .holder__name { font-weight: 700; font-size: 23px; line-height: 1; letter-spacing: 0.1px; }
  .holder__role { font-weight: 400; font-size: 13.5px; margin-top: 6px; }

  .brand-seal {
    position: absolute; border-radius: 50%;
    display: flex; align-items: center; justify-content: center; text-align: center;
    font-weight: 500; text-transform: uppercase;
  }
  .brand-seal--small {
    left: 426px; top: 33px; width: 128px; height: 128px;
    border: 1px solid var(--ring-grey); color: var(--ink);
    font-size: 12px; letter-spacing: 1.5px; line-height: 1.45;
  }
  .brand-seal--large {
    left: 171px; top: 67px; width: 254px; height: 254px;
    border: 1px solid var(--cream); color: var(--cream);
    font-size: 22px; letter-spacing: 3px; line-height: 1.45;
  }

  .contact-list { position: absolute; left: 30px; top: 252px; list-style: none; }
  .contact-list li {
    display: flex; align-items: center; height: 21.5px;
    font-size: 13.5px; font-weight: 400;
  }
  .contact-list .icon { width: 13px; height: 13px; margin-right: 7px; flex: none; }
  .contact-list .dot { width: 12px; height: 12px; border-radius: 50%; background: var(--ink); margin-right: 8px; flex: none; }

  .address {
    position: absolute; left: 406px; top: 301px;
    font-size: 13.5px; line-height: 16.5px; font-style: normal;
  }
</style>
</head>
<body>
<div class="canvas">
  <section class="card card--front">
    <div class="holder">
      <h1 class="holder__name">Corinne Haldwick</h1>
      <p class="holder__role">Owner</p>
    </div>

    <div class="brand-seal brand-seal--small">Rosalind<br>Thorpe<br>Gardens</div>

    <ul class="contact-list">
      <li>
        <svg class="icon" viewBox="0 0 24 24" aria-hidden="true"><path fill="#0b2a30" d="M6.6 10.8c1.4 2.8 3.8 5.1 6.6 6.6l2.2-2.2c.3-.3.7-.4 1-.2 1.1.4 2.3.6 3.6.6.6 0 1 .4 1 1V20c0 .6-.4 1-1 1C10.6 21 3 13.4 3 4c0-.6.4-1 1-1h3.5c.6 0 1 .4 1 1 0 1.3.2 2.5.6 3.6.1.3 0 .7-.2 1z"/></svg>
        913-555-0147
      </li>
      <li><span class="dot"></span>Rosalind Thorpe Gardens</li>
      <li><span class="dot"></span>@RosalindThorpeGardens</li>
      <li>
        <svg class="icon" viewBox="0 0 24 24" aria-hidden="true"><circle cx="12" cy="12" r="10" fill="none" stroke="#0b2a30" stroke-width="2"/><ellipse cx="12" cy="12" rx="4" ry="10" fill="none" stroke="#0b2a30" stroke-width="2"/><path d="M2 12h20" stroke="#0b2a30" stroke-width="2"/></svg>
        www.RosalindThorpeGardens.example
      </li>
    </ul>

    <address class="address">418 Meadowlark Ln, #112<br>Larkfield, KS 66025</address>
  </section>

  <section class="card card--back">
    <div class="brand-seal brand-seal--large">Rosalind<br>Thorpe<br>Gardens</div>
  </section>
</div>
</body>
</html>
```